Weightloss company needs Business Card

We want a business card that is clean and professional, yet portrays that we are a friendly, innovative, and versatile program designed to fit the needs of our clients.
I would like there to be 2 sides, one side having an appointment card, and the other side containing the logo and business information. There can be decorations on both sides. The logo is attached.

Target Market(s)

Men and women 40-60

Industry/Entity Type

Business

Contact Information for Business Card

Font styles to use
Sans Serif

Requirements
Must have
• The logo, space for business information
Nice to have
• The colors in the logo
Should not have
• No pictures of people or food

```html
<!DOCTYPE html>
<html lang="en">
<head>
<meta charset="utf-8">
<title>Risewell Weightloss – Business Card</title>
<link rel="stylesheet" href="https://fonts.googleapis.com/css2?family=Open+Sans:wght@400;600;700&display=swap">
<style>
  :root {
    --brand-red: #e8102e;
    --ink: #2b2b2b;
    --muted: #555555;
    --rule: #bdbdbd;
    --card: #ffffff;
    --backdrop: #3a3d42;
  }
  * { box-sizing: border-box; margin: 0; padding: 0; }
  html, body {
    width: 1200px; height: 864px; overflow: hidden;
    background: var(--backdrop);
    font-family: "Open Sans", Arial, sans-serif;
  }
  .canvas { position: relative; width: 1200px; height: 864px; }
  .card {
    position: absolute; width: 560px; height: 320px;
    background: var(--card); overflow: hidden;
    box-shadow: 0 10px 30px rgba(0,0,0,.35);
  }

  /* Appointment side */
  .appointment-card { left: 70px; top: 70px; }
  .brand-mark {
    display: flex; align-items: center; gap: 8px;
    color: var(--brand-red); font-weight: 700; font-size: 22px; line-height: 1;
  }
  .brand-mark .dot {
    width: 14px; height: 14px; border-radius: 50%; background: var(--brand-red);
  }
  .appointment-card .brand-mark { justify-content: center; margin-top: 30px; }
  .appointment-title {
    text-align: center; color: var(--brand-red);
    font-weight: 600; font-size: 20px; margin-top: 18px;
  }
  .field-list { margin: 16px 0 0 70px; width: 420px; }
  .field {
    display: flex; align-items: flex-end; height: 30px;
    color: var(--brand-red); font-weight: 600; font-size: 13px;
  }
  .field .fill { flex: 1; border-bottom: 2px dotted var(--ink); margin-left: 6px; height: 12px; }
  .field .meridiem { color: var(--ink); font-weight: 600; font-size: 13px; margin-left: 2px; }
  .notice-band {
    position: absolute; left: 0; right: 0; bottom: 30px; height: 36px;
    background: var(--brand-red); color: #fff;
    display: flex; align-items: center; justify-content: center;
    font-weight: 600; font-size: 13.5px;
  }

  /* Contact side */
  .contact-card { left: 570px; top: 470px; }
  .contact-card .brand-mark { position: absolute; right: 40px; top: 52px; font-size: 26px; }
  .person { position: absolute; left: 34px; top: 98px; }
  .person-name { color: var(--brand-red); font-weight: 600; font-size: 21px; line-height: 1.1; }
  .person-role { color: var(--muted); font-size: 12.5px; }
  .divider {
    position: absolute; left: 180px; right: 40px; top: 150px;
    border-top: 1px solid var(--rule);
  }
  .contact-list {
    position: absolute; right: 40px; top: 176px; list-style: none;
    text-align: right; color: var(--ink); font-size: 14px;
  }
  .contact-list li { display: flex; align-items: center; justify-content: flex-end; gap: 10px; height: 22px; }
  .contact-list svg { width: 12px; height: 12px; fill: none; stroke: var(--brand-red); stroke-width: 2; }
  .contact-list svg .solid { fill: var(--brand-red); stroke: none; }
</style>
</head>
<body>
<main class="canvas">

  <section class="card appointment-card" aria-label="Appointment card">
    <div class="brand-mark"><span class="dot"></span>Risewell Weightloss</div>
    <h2 class="appointment-title">Your Next Appointment is</h2>
    <div class="field-list">
      <div class="field">Name:<span class="fill"></span></div>
      <div class="field">Date:<span class="fill"></span></div>
      <div class="field">Time:<span class="fill"></span><span class="meridiem">AM</span><span class="fill"></span><span class="meridiem">PM</span></div>
    </div>
    <div class="notice-band">If unable to keep appointment, kindly give 24hrs notice.</div>
  </section>

  <section class="card contact-card" aria-label="Contact card">
    <div class="brand-mark"><span class="dot"></span>Risewell Weightloss</div>
    <div class="person">
      <p class="person-name">Daniel Carter</p>
      <p class="person-role">Managing Director</p>
    </div>
    <div class="divider"></div>
    <ul class="contact-list">
      <li>044-555-0142
        <svg viewBox="0 0 12 12" aria-hidden="true"><path class="solid" d="M2 1l2 0 1 3-1.5 1a6 6 0 0 0 3.5 3.5L8 7l3 1v2a1 1 0 0 1-1 1A9 9 0 0 1 1 2a1 1 0 0 1 1-1z"/></svg></li>
      <li>123-555-0178
        <svg viewBox="0 0 12 12" aria-hidden="true"><rect class="solid" x="1" y="4" width="10" height="6" rx="1"/><rect x="3" y="1" width="6" height="3"/></svg></li>
      <li>123-555-0193
        <svg viewBox="0 0 12 12" aria-hidden="true"><rect x="3" y="1" width="6" height="10" rx="1"/></svg></li>
      <li>hello@risewellclinic.com
        <svg viewBox="0 0 12 12" aria-hidden="true"><rect class="solid" x="1" y="2.5" width="10" height="7"/><path d="M1 3l5 3.5L11 3" stroke="#fff" stroke-width="1"/></svg></li>
      <li>www.risewellclinic.com
        <svg viewBox="0 0 12 12" aria-hidden="true"><path d="M5 7l2-2M4 6L2.5 7.5a2 2 0 0 0 2 2L6 8M8 6l1.5-1.5a2 2 0 0 0-2-2L6 4"/></svg></li>
    </ul>
  </section>

</main>
</body>
</html>
```